New web design for a service provider in the medical field

We are looking for a new design for our website. We are a company that repairs and sells medical endoscopes. Our customers include doctors and hospitals. Our current website can be found at https://lumavex.de/en/lumavex-english.
We need a new web design (without programming) for the following 3 pages:
-Startpage https://lumavex.de/en/lumavex-english/
-Used endoscopes https://lumavex.de/en/used-endoscopes/
-Purchase https://lumavex.de/en/purchase/
The design should be modern and stylish.
The blue color of the logo should be reflected on the page, but not too intrusive.
I have uploaded the images from the header. If more images are needed, let me know and I will upload them.

Target Market(s)
Doctors and hospitals

```html
<!DOCTYPE html>
<html lang="en">
<head>
<meta charset="utf-8">
<title>Lumavex – Sell your endoscope</title>
<link href="https://fonts.googleapis.com/css2?family=Red+Hat+Display:wght@400;500;600;700;800&display=swap" rel="stylesheet">
<style>
:root{
  --navy:#0b1a6e;
  --ink:#1d1d2b;
  --muted:#8a8f98;
  --field:#e6e9ec;
  --line:#e3e6ea;
  --accent:#12b4ee;
  --button:#35b3fb;
  --band-a:#0a2896;
  --band-b:#0479bc;
  --hero:#dfe3e7;
  --white:#ffffff;
}
*{box-sizing:border-box;margin:0;padding:0}
html,body{width:1200px;height:3420px;overflow:hidden;background:var(--white)}
body{position:relative;font-family:"Red Hat Display",sans-serif;color:var(--ink)}
.abs{position:absolute}

/* header */
.brand{left:120px;top:62px;display:flex;align-items:center;gap:10px;font-size:26px;font-weight:700;color:var(--navy)}
.brand-dot{width:18px;height:18px;border-radius:50%;background:var(--accent)}
.topbar{top:30px;right:460px;font-size:11px;color:var(--muted);display:flex;gap:36px;align-items:center}
.topbar{left:778px;right:auto}
.topbar span{display:flex;align-items:center;gap:8px}
.nav{top:116px;left:593px;font-size:14px;font-weight:600;color:var(--ink)}
.nav a{position:absolute;white-space:nowrap;color:inherit;text-decoration:none}
.nav .active{color:var(--navy);border-bottom:2px solid var(--accent);padding-bottom:2px}

/* hero */
.hero{left:0;top:174px;width:1200px;height:235px;background:var(--hero)}
.hero-photo{left:624px;top:174px;width:576px;height:235px;background:linear-gradient(110deg,#dfe3e7 0%,#cfd4da 35%,#9aa1aa 60%,#e9ecef 100%)}
.crumb{left:127px;top:193px;font-size:11px;color:var(--muted)}
.crumb b{color:var(--accent);font-weight:500}
.accent-bar{height:6px;width:80px;background:var(--accent)}
.hero-title{left:123px;top:294px;font-size:47px;font-weight:800;color:var(--navy);letter-spacing:-.5px}
.hero-sub{left:123px;top:350px;font-size:28px;font-weight:500;color:var(--navy)}

/* form */
.card{left:85px;top:451px;width:1038px;height:1177px;border:1px solid var(--line);border-radius:18px}
.section-label{left:142px;font-size:14px;font-weight:700;font-style:italic;color:var(--navy);width:844px;border-bottom:1px solid var(--line);padding-bottom:8px}
.field{height:35px;background:var(--field);border-radius:6px;font-size:14px;color:var(--muted);padding:0 24px;display:flex;align-items:center;justify-content:space-between}
.caret{font-size:8px;color:#666}
.remarks{align-items:flex-start;padding-top:12px}
.check{left:357px;top:1457px;width:21px;height:21px;background:var(--field);border-radius:4px}
.consent{left:406px;top:1455px;width:600px;font-size:13.5px;line-height:15.5px;letter-spacing:.6px;color:#444}
.send{left:620px;top:1557px;width:383px;height:31px;border-radius:16px;background:var(--navy);color:var(--white);font-size:14px;font-weight:700;letter-spacing:1px;display:flex;align-items:center;justify-content:center}

/* why us */
.band{left:0;top:1752px;width:1200px;height:931px;background:linear-gradient(160deg,var(--band-a) 0%,var(--band-b) 100%)}
.band-title{left:125px;top:1834px;font-size:50px;font-weight:800;color:var(--white)}
.reason{width:330px;text-align:center;color:var(--white)}
.reason h3{font-size:28px;font-weight:500;margin-bottom:12px}
.reason p{font-size:14.5px;line-height:16.5px;width:240px;margin:0 auto;letter-spacing:.2px}

/* contact */
.help{width:470px;text-align:center}
.help h2{font-size:40px;font-weight:700;margin-top:14px}
.help p{font-size:14px;letter-spacing:.8px;line-height:16px;color:#444;margin-top:18px}
.divider{left:601px;top:2817px;width:1px;height:232px;background:#5d8fd4}
.cta{top:3018px;width:465px;height:42px;border-radius:21px;background:var(--button);color:var(--white);font-size:11px;font-weight:700;letter-spacing:.5px;display:flex;align-items:center;justify-content:center;box-shadow:0 4px 8px rgba(0,0,0,.12)}

/* footer */
.foot-brand{left:0;width:1200px;top:3170px;text-align:center;font-size:18px;font-weight:700;color:var(--navy)}
.foot-tag{left:0;width:1200px;top:3196px;text-align:center;font-size:8px;color:var(--accent)}
.social{left:562px;top:3260px;display:flex;gap:26px}
.social i{width:10px;height:10px;border-radius:50%;background:#555;display:block}
.flags{top:3306px;left:560px;display:flex;gap:30px;align-items:center}
.flag-wrap{padding:6px 14px;border-radius:14px}
.flag-wrap.on{background:#eceff2}
.foot-links{top:3358px;left:375px;font-size:10.5px;color:#777;display:flex;gap:26px}
.badge{left:1085px;top:3328px;width:52px;height:37px;background:#2b5fb3;border-radius:3px}
.to-top{left:1167px;top:3340px;font-size:14px;color:#aaa}
.copy{left:0;top:3384px;width:1200px;height:36px;background:#ececec;font-size:10.5px;color:#777;display:flex;align-items:center;justify-content:center}
</style>
</head>
<body>

<!-- header -->
<div class="abs brand"><span class="brand-dot"></span>Lumavex</div>
<div class="abs topbar">
  <span><svg width="11" height="9" viewBox="0 0 11 9"><rect x=".5" y=".5" width="10" height="8" fill="none" stroke="#999"/><path d="M.5 .5l5 4 5-4" fill="none" stroke="#999"/></svg>info@lumavex.de</span>
  <span><svg width="10" height="10" viewBox="0 0 10 10"><path d="M2 0l2 2-1 2 3 3 2-1 2 2-2 2C4 10 0 6 0 2z" fill="#999"/></svg>+49 4100 555 120-0</span>
  <span style="gap:10px"><span class="caret">▼</span><svg width="22" height="14" viewBox="0 0 22 14"><rect width="22" height="14" fill="#fff"/><g fill="#c8232c"><rect y="0" width="22" height="2"/><rect y="4" width="22" height="2"/><rect y="8" width="22" height="2"/><rect y="12" width="22" height="2"/></g><rect width="10" height="8" fill="#1f3a93"/></svg></span>
</div>
<nav class="abs nav">
  <a class="active" style="left:0">Home</a>
  <a style="left:92px">Buy Used Endoscopes</a>
  <a style="left:305px">Sell Your Endoscope</a>
  <a style="left:486px"><span class="caret">▼</span>&nbsp; Other</a>
</nav>

<!-- hero -->
<div class="abs hero"></div>
<div class="abs hero-photo" role="img" aria-label="Close-up photo of an endoscope control handle with angulation knobs"></div>
<div class="abs crumb"><b>Home</b> / Sell Endoscpes</div>
<div class="abs accent-bar" style="left:127px;top:276px"></div>
<h1 class="abs hero-title">Sell your endoscope</h1>
<div class="abs hero-sub">Fair price – Full performances</div>

<!-- form -->
<div class="abs card"></div>
<div class="abs section-label" style="top:522px">Personal informations</div>
<div class="abs field" style="left:357px;top:582px;width:153px">Salutation <span class="caret">▼</span></div>
<div class="abs field" style="left:730px;top:582px;width:153px">Position</div>
<span class="abs caret" style="left:917px;top:595px">▼</span>
<div class="abs field" style="left:356px;top:646px;width:276px">Firstname</div>
<div class="abs field" style="left:730px;top:646px;width:276px">Lastname</div>
<div class="abs field" style="left:356px;top:709px;width:276px">Email</div>
<div class="abs field" style="left:730px;top:709px;width:276px">Phone</div>

<div class="abs section-label" style="top:795px">Informations about the device</div>
<div class="abs field" style="left:357px;top:859px;width:275px">Brand <span class="caret">▼</span></div>
<div class="abs field" style="left:732px;top:859px;width:274px">Model <span class="caret">▼</span></div>
<div class="abs field" style="left:356px;top:921px;width:650px">Defects</div>
<div class="abs field" style="left:356px;top:984px;width:168px;padding-left:21px">Asking price</div>
<div class="abs field" style="left:536px;top:984px;width:96px;padding-left:38px;color:#333">€ <span class="caret">▼</span></div>

<div class="abs section-label" style="top:1071px">Remarks and picture</div>
<div class="abs field" style="left:356px;top:1152px;width:168px;padding-left:19px">Upload picture</div>
<div class="abs field remarks" style="left:356px;top:1242px;width:650px;height:146px;padding-left:22px">Remarks</div>

<div class="abs check"></div>
<p class="abs consent">I have read the privacy policy and accept it. I agree above input will be transmitted to Lumavex GmbH to get in contact with me respectively to process my request and store all needed informations. Neither a transfer to third parties will happen, nor a use for advertising purposes by Lumavex GmbH!</p>
<div class="abs send">SEND</div>

<!-- why us -->
<section class="abs band"></section>
<h2 class="abs band-title">Why Us?</h2>
<div class="abs accent-bar" style="left:127px;top:1905px"></div>

<div class="abs reason" style="left:98px;top:2052px"><h3>Cost Efficient</h3><p>Our regular stock includes refurbished gastroscopes, colo­scopes, bronchoscopes, cystoscopes and duodenoscopes from the well-known manufacturers Orvanta, Pellix and Fujaro.</p></div>
<div class="abs reason" style="left:424px;top:2052px"><h3>No Maintenance Contract</h3><p>Our regular stock includes refurbished gastroscopes, colo­scopes, bronchoscopes, cystoscopes and duodenoscopes from the well-known manufacturers Orvanta, Pellix and Fujaro.</p></div>
<div class="abs reason" style="left:808px;top:2052px"><h3>German Quality</h3><p>Our regular stock includes refurbished gastroscopes, colo­scopes, bronchoscopes, cystoscopes and duodenoscopes from the well-known manufacturers Orvanta.</p></div>

<div class="abs reason" style="left:98px;top:2345px"><h3>Cost Efficient</h3><p>Our regular stock includes refurbished gastroscopes, colo­scopes, bronchoscopes, cystoscopes and duodenoscopes from the well-known manufacturers Orvanta, Pellix and Fujaro.</p></div>
<div class="abs reason" style="left:424px;top:2345px"><h3>No Maintenance Contract</h3><p>Our regular stock includes refurbished gastroscopes, colo­scopes, bronchoscopes, cystoscopes and duodenoscopes from the well-known manufacturers Orvanta, Pellix and Fujaro.</p></div>
<div class="abs reason" style="left:808px;top:2345px"><h3>German Quality</h3><p>Our regular stock includes refurbished gastroscopes, colo­scopes, bronchoscopes, cystoscopes and duodenoscopes from the well-known manufacturers Orvanta.</p></div>

<!-- contact -->
<div class="abs help" style="left:78px;top:2770px">
  <svg width="50" height="40" viewBox="0 0 50 40"><rect x="2" y="2" width="46" height="36" fill="none" stroke="#d0d3d8" stroke-width="3"/><path d="M2 2l23 20L48 2M2 38l17-17M48 38L31 21" fill="none" stroke="#d0d3d8" stroke-width="3"/></svg>
  <h2>We'll help you!</h2>
  <p>Discover classic and brand new styles in a variety of shapes, colours and materials, from signature Frame to the latest teardrop inspired watches.</p>
</div>
<div class="abs divider"></div>
<div class="abs help" style="left:662px;top:2765px">
  <svg width="76" height="50" viewBox="0 0 76 50"><path d="M8 4l10 10-5 6c3 8 8 13 16 17l6-5 10 10-6 6C20 48 2 28 2 10z" fill="#d0d3d8"/><path d="M50 20a12 12 0 0 1 10 14M52 10a22 22 0 0 1 18 24" fill="none" stroke="#d0d3d8" stroke-width="3"/></svg>
  <h2>Call Us</h2>
  <p>+49 4100 555 120-0</p>
  <p style="margin-top:8px">Monday - Friday<br>8AM - 20AM UTC</p>
</div>
<div class="abs cta" style="left:80px">CONTACT US</div>
<div class="abs cta" style="left:664px">CALL NOW</div>

<!-- footer -->
<div class="abs foot-brand">Lumavex</div>
<div class="abs foot-tag">Results that really matter</div>
<div class="abs social"><i></i><i></i><i></i></div>
<div class="abs flags">
  <span class="flag-wrap"><svg width="22" height="14" viewBox="0 0 22 14"><rect width="22" height="5" fill="#111"/><rect y="4.7" width="22" height="4.7" fill="#d8262c"/><rect y="9.3" width="22" height="4.7" fill="#f4c400"/></svg></span>
  <span class="flag-wrap on"><svg width="22" height="14" viewBox="0 0 22 14"><rect width="22" height="14" fill="#fff"/><g fill="#c8232c"><rect width="22" height="2"/><rect y="4" width="22" height="2"/><rect y="8" width="22" height="2"/><rect y="12" width="22" height="2"/></g><rect width="10" height="8" fill="#1f3a93"/></svg></span>
</div>
<div class="abs foot-links"><span>Home</span><span>Repair</span><span>Buy</span><span>Sell</span><span>pick-up order</span><span>about us</span><span>contact us</span></div>
<div class="abs badge"></div>
<div class="abs to-top">↑</div>
<div class="abs copy">Copyright © 2022 Lumavex GmbH. Use of this website constitutes acceptance of our User Agreement and Privacy Policy.</div>

</body>
</html>
```